Client Fund Fact Sheet Flyer - Investment Advisory

We require this 3 page flyer document polished and made to look professional by a designer. There may be repeat work for the . The logo is provided in the uploaded files and the colour codes and fonts to be used are: Colour - Orange
PMS 144
RGB (222, 135, 3)
#de8703

Colour - Grey
PMS 432
RGB (51,51,51)
#333333

Fonts
Family: Helvetica Neue
Cuts: 57 Condensed
67 Medium Condensed

Target Market(s)

Clients of an investment management firm

Industry/Entity Type

Investment Advisory

Font styles to use
Other font styles liked:
• Helvetica Neue

Requirements
Must have
• Tables and charts, look professional
Should not have
• Should not look like it was made in word or publisher by us!

```html
<!DOCTYPE html>
<html lang="en">
<head>
<meta charset="utf-8">
<title>Balanced Growth – Investment Beliefs</title>
<link href="https://fonts.googleapis.com/css2?family=Bebas+Neue&family=Carlito:wght@400;700&family=Roboto:wght@400;700&display=swap" rel="stylesheet">
<style>
  :root{
    --orange:#de8703;
    --orange-bright:#ee7f0d;
    --grey:#333333;
    --slate:#3e4650;
    --text-soft:#555555;
    --tint:#fce4cc;
    --tint-light:#fdf3e7;
  }
  *{box-sizing:border-box;margin:0;padding:0}
  html,body{width:848px;height:1200px;overflow:hidden;background:#fff}
  .page{position:relative;width:848px;height:1200px;font-family:"Roboto",Arial,sans-serif;color:var(--grey)}
  .top-band{position:absolute;left:0;top:0;width:848px;height:20px;background:var(--orange)}
  .issue-date{position:absolute;left:65px;top:43px;font-weight:700;font-size:14px;color:#111}
  .fund-title{position:absolute;left:60px;top:72px;font-family:"Bebas Neue",sans-serif;font-size:74px;line-height:1;color:var(--orange);letter-spacing:-0.5px}
  .brand-name{position:absolute;right:50px;top:30px;font-family:"Roboto",sans-serif;font-weight:700;font-size:38px;color:var(--orange);letter-spacing:-1px}
  .section-band{position:absolute;left:59px;top:147px;width:739px;height:35px;background:var(--tint-light);padding-left:4px;font-weight:700;font-size:19px;line-height:35px;color:#111}
  .approach{position:absolute;left:57px;top:224px;width:740px;height:186px;border:1.5px solid var(--orange-bright)}
  .approach-head{margin-top:15px;height:23px;background:var(--orange-bright);color:#fff;text-align:center;font-size:15px;line-height:24px;letter-spacing:.3px}
  .approach-body{padding:10px 24px 0 24px;font-size:14px;line-height:21px;color:var(--text-soft)}
  .approach-body p{margin-bottom:4px}
  .beliefs{position:absolute;left:53px;top:428px;width:739px}
  .beliefs-head{display:grid;grid-template-columns:264px 243px 232px;height:35px}
  .beliefs-head span{background:var(--orange);color:#111;font-family:"Carlito",sans-serif;font-weight:700;font-size:11px;display:flex;align-items:center;justify-content:center;margin-left:2px}
  .beliefs-head span:first-child{background:none}
  .belief-row{display:grid;grid-template-columns:130px 132px 245px 232px;border-bottom:1px dotted #ddd;font-family:"Carlito",sans-serif;font-size:10.5px;line-height:14px;color:#222}
  .belief-row>div{display:flex;align-items:center;margin-right:2px}
  .belief-row.shaded>div{background:var(--tint)}
  .belief-icon{justify-content:center}
  .belief-name{justify-content:center;text-align:center;font-weight:700;font-size:10.5px;padding:0 10px}
  .belief-text,.belief-principle{padding:0 12px;text-align:justify}
  .belief-principle{margin-right:0!important}
  .dollar{font-family:"Roboto",sans-serif;font-weight:700;font-size:56px;color:var(--orange)}
  .disclaimer{position:absolute;left:147px;top:1162px;font-size:8px;line-height:10.5px;font-style:italic;color:var(--orange)}
  .foot-orange{position:absolute;left:0;top:1184px;width:143px;height:16px;background:var(--orange)}
  .foot-slate{position:absolute;left:146px;top:1184px;width:702px;height:16px;background:var(--slate)}
</style>
</head>
<body>
<div class="page">
  <div class="top-band"></div>
  <div class="issue-date">19 March 2021</div>
  <h1 class="fund-title">BALANCED GROWTH</h1>
  <div class="brand-name">summit</div>
  <div class="section-band">Investment Beliefs</div>

  <section class="approach">
    <div class="approach-head">OUR APPROACH</div>
    <div class="approach-body">
      <p>Our investment approach aims to deliver strong long-term investment returns, over and above inflation, to help you build your wealth.</p>
      <p>We carefully consider investments and expose our clients to risk only when we believe will be adequately rewarded.</p>
      <p>We take an objective approach to investment selection and have no bias towards any type of investment.</p>
    </div>
  </section>

  <section class="beliefs">
    <div class="beliefs-head"><span></span><span>Belief</span><span>Principle</span></div>

    <div class="belief-row shaded" style="height:154px">
      <div class="belief-icon"><span class="dollar">$</span></div>
      <div class="belief-name">1. Economic or Exceptional</div>
      <div class="belief-text">Above market returns can be achieved by active managers who possess skill and experience. It is challenging however to reliably identify skillful managers in advance.</div>
      <div class="belief-principle">A high bar will be set for the inclusion of active management and we will seek to access the best ideas from external fund managers. The default allocation will be through an index and fees paid where there is high conviction of excess return potential or diversification benefits.</div>
    </div>

    <div class="belief-row" style="height:97px">
      <div class="belief-icon"><svg width="44" height="44" viewBox="0 0 44 44"><path d="M20 4 A19 19 0 1 0 39 23 L20 23 Z" fill="var(--orange)"/><path d="M23 1 A19 19 0 0 1 42 20 L23 20 Z" fill="var(--orange)"/><path d="M24 24 L40 24 A19 19 0 0 1 36 35 Z" fill="#fff" stroke="var(--orange)" stroke-width="2"/></svg></div>
      <div class="belief-name">2. Diversify<br>where it counts</div>
      <div class="belief-text">Genuine portfolio diversification is the primary tool available to manage risk.</div>
      <div class="belief-principle">Diversification should be achieved by investing across different asset classes, and within asset classes by accessing a range of managers and strategies.</div>
    </div>

    <div class="belief-row shaded" style="height:70px">
      <div class="belief-icon"><svg width="40" height="38" viewBox="0 0 40 38" fill="var(--orange)"><rect x="1" y="10" width="11" height="5"/><rect x="14" y="10" width="11" height="5"/><rect x="1" y="18" width="6" height="5"/><rect x="9" y="18" width="11" height="5"/><rect x="22" y="18" width="11" height="5"/><rect x="35" y="18" width="4" height="5"/><rect x="1" y="26" width="11" height="5"/><rect x="14" y="26" width="11" height="5"/><rect x="27" y="26" width="12" height="5"/><rect x="1" y="33" width="6" height="5"/><rect x="9" y="33" width="11" height="5"/><rect x="22" y="33" width="11" height="5"/><rect x="35" y="33" width="4" height="5"/><path d="M28 6 L38 1 L39 4 L29 9 Z"/></svg></div>
      <div class="belief-name">3.Client Centric Risk Setting</div>
      <div class="belief-text">Risk for Summit's clients is primarily the risk of permanent capital loss.</div>
      <div class="belief-principle">Risk will be defined and measured as the magnitude of a severe loss in portfolio construction.</div>
    </div>

    <div class="belief-row" style="height:75px">
      <div class="belief-icon"><svg width="38" height="42" viewBox="0 0 38 42" fill="none" stroke="var(--orange)"><path d="M9 2 H29 V14 A10 10 0 0 1 9 14 Z" fill="var(--orange)" stroke="none"/><path d="M9 5 H3 V10 A7 7 0 0 0 10 17 M29 5 H35 V10 A7 7 0 0 1 28 17" stroke-width="3"/><rect x="17" y="24" width="4" height="10" fill="var(--orange)" stroke="none"/><rect x="8" y="36" width="22" height="5" fill="var(--orange)" stroke="none"/></svg></div>
      <div class="belief-name">4. A competitive offering</div>
      <div class="belief-text">Our clients expect to achieve strong investment results from investing with us compared to other options.</div>
      <div class="belief-principle">Portfolios will be benchmarked against publicly available surveys of competing offerings.</div>
    </div>

    <div class="belief-row shaded" style="height:91px">
      <div class="belief-icon"><svg width="46" height="30" viewBox="0 0 46 30" fill="var(--orange)"><path d="M1 7 L9 2 L14 11 L6 16 Z"/><path d="M45 7 L37 2 L32 11 L40 16 Z"/><path d="M13 8 L21 5 L27 7 L33 6 L37 13 L30 22 L25 27 L21 27 L11 17 Z"/></svg></div>
      <div class="belief-name">5.Partner with Professionals</div>
      <div class="belief-text">Listening to external expertise will lead to stronger investment outcomes for our clients.</div>
      <div class="belief-principle">We will engage professional portfolio construction and asset management expertise to both select agents and invest in securities for our clients.</div>
    </div>

    <div class="belief-row" style="height:59px">
      <div class="belief-icon" style="align-items:flex-start"><svg width="50" height="36" viewBox="0 0 50 36"><path d="M2 17 L17 32 L48 2" fill="none" stroke="var(--orange)" stroke-width="5"/></svg></div>
      <div class="belief-name">6.Keep it Simple</div>
      <div class="belief-text">Good ideas get lost in complexity. Our clients deserve to understand where their savings are invested.</div>
      <div class="belief-principle">Portfolios will be only as complicated as required to achieve risk and return objectives.</div>
    </div>

    <div class="belief-row shaded" style="height:91px">
      <div class="belief-icon"><svg width="40" height="36" viewBox="0 0 40 36" fill="var(--orange)"><path d="M3 36 V31 H17 V36 Z M5 30 C5 24 10 22 8 18 L3 16 L4 11 L9 4 L12 0 L13 4 C18 6 18 18 16 30 Z"/><path d="M22 36 V31 H39 V36 Z M24 30 L26 14 H35 L37 30 Z M23 12 V2 H26 V5 H29 V2 H32 V5 H35 V2 H38 V12 Z"/></svg></div>
      <div class="belief-name">7.Be Patient</div>
      <div class="belief-text">Markets are not always efficiently priced, but it is challenging to identify opportunities to take advantage of mispricing.</div>
      <div class="belief-principle">We will set diversified strategic asset allocations that reflect the risk appetites and time horizons of our clients. Active decisions will be focused on managing risk to our clients.</div>
    </div>
  </section>

  <p class="disclaimer">This document relates to the Summit Financial Group Managed Models for which Harbourline has appointed Meridian Capital Pty Ltd (ABN 00 000 000 000)<br>(‘Meridian Capital’), an Authorised representative of AFS Licence No. 000000 as the Model Manager.</p>
  <div class="foot-orange"></div>
  <div class="foot-slate"></div>
</div>
</body>
</html>
```